kmvalerohub website

I need a new homepage design for my current website at www.KMValeroHub.com. I want someone to look at my current website and develop a more appealing homepage... right now the colors don't blend very well and it needs a facelift

Reason: This has been extended to September 10th

```html
<!DOCTYPE html>
<html lang="en">
<head>
<meta charset="utf-8">
<title>KM Valero – Home</title>
<link href="https://fonts.googleapis.com/css2?family=Open+Sans:ital,wght@0,400;0,600;0,700;1,400&display=swap" rel="stylesheet">
<style>
:root{
  --teal:#6fc4b3;
  --teal-dark:#5fb3a3;
  --teal-deep:#3f8f86;
  --red:#e9534c;
  --grey-bg:#efefef;
  --grey-band:#e6e6e6;
  --grey-frame:#c3c6c8;
  --text:#555;
  --white:#fff;
}
*{box-sizing:border-box;margin:0;padding:0}
html,body{width:930px;height:1200px;overflow:hidden}
body{position:relative;font-family:'Open Sans',sans-serif;background:var(--grey-bg);color:var(--text)}
.abs{position:absolute}

.site-header{left:0;top:0;width:930px;height:48px;background:var(--teal)}
.brand{left:112px;top:9px;font-size:24px;color:var(--white);font-weight:400}
.main-nav{right:100px;top:14px;display:flex;align-items:center}
.main-nav a{color:var(--white);font-size:9.5px;font-weight:600;text-decoration:none;padding:5px 10px;text-transform:uppercase}
.main-nav a.active{background:var(--teal-deep);border-radius:2px}
.search-icon{right:96px;top:18px}

.hero{left:0;top:48px;width:930px;height:312px;background:linear-gradient(180deg,#3aa7e6 0%,#8fd0f4 55%,#bfe5f6 68%,#6cb83a 74%,#4e9a24 100%)}
.hero-person-left{left:180px;top:82px;width:115px;height:278px;background:linear-gradient(180deg,#5a3a2e,#3a3a3a);border-radius:40px 40px 0 0;opacity:.85}
.hero-person-right{left:608px;top:48px;width:160px;height:312px;background:linear-gradient(180deg,#c99a7a,#f1eeea);border-radius:60px 60px 0 0;opacity:.85}
.hero-title{left:379px;top:150px;width:171px;height:30px;background:var(--red);color:var(--white);font-size:20px;font-weight:700;text-align:center;line-height:30px;border-radius:2px}
.hero-text{left:319px;top:186px;width:292px;height:44px;background:rgba(50,95,110,.75);color:var(--white);font-size:11px;text-align:center;padding:7px 10px;line-height:1.45}
.hero-arrow{top:186px;width:30px;height:36px;background:var(--red);display:flex;align-items:center;justify-content:center}
.hero-arrow.prev{left:0}.hero-arrow.next{right:0}

.slider-dots{left:403px;top:372px;display:flex;gap:50px}
.slider-dots span{width:38px;height:3px;background:#bbb}

.report{left:102px;top:390px;width:724px;height:76px;background:#e8e8e8;border-radius:3px}
.report-book{left:108px;top:374px;width:72px;height:100px;background:linear-gradient(135deg,#d8322c,#f4f4f4 60%,#c22);border-radius:2px}
.report-label{left:188px;top:394px;font-size:11px;font-weight:700;color:var(--red);line-height:1.35}
.report-note{left:188px;top:422px;font-size:8.5px;color:#444}
.report-form{left:188px;top:439px;display:flex;align-items:center;font-size:10px;font-weight:700;color:#444}
.report-form .field{width:120px;height:12px;border:1px solid #777;background:var(--white);margin:0 10px 0 4px}
.subscribe{background:var(--red);color:var(--white);font-size:8.5px;font-weight:700;padding:5px 8px;border-radius:2px}
.privacy{left:592px;top:418px;width:200px;font-size:8px;font-style:italic;color:#666;line-height:1.4}

.why-band{left:0;top:486px;width:930px;height:246px;background:var(--grey-band)}
.why-title{left:0;top:520px;width:930px;text-align:center;font-size:26px;font-weight:600;color:var(--red)}
.why-sub{left:0;top:553px;width:930px;text-align:center;font-size:8.5px;color:#555}

.card{background:var(--grey-frame);border-radius:4px;padding:24px 3px 3px}
.card .dots{position:absolute;left:8px;top:9px;display:flex;gap:4px}
.card .dots i{width:6px;height:6px;border-radius:50%;background:var(--white)}
.card .bar{position:absolute;right:8px;top:11px;width:7px;height:2px;background:var(--white)}
.card .photo{width:100%;height:100%}
.card-left{left:101px;top:642px;width:190px;height:160px}
.card-right{left:636px;top:642px;width:190px;height:160px}
.card-main{left:288px;top:604px;width:352px;height:222px;box-shadow:0 2px 6px rgba(0,0,0,.25)}

.clients-title{left:102px;top:851px;font-size:11px;font-weight:700;color:#666}
.clients-rule{left:212px;top:859px;width:540px;height:1px;background:#ddd}
.clients-nav{top:846px;width:26px;height:24px;border-radius:2px;display:flex;align-items:center;justify-content:center}
.clients-nav.prev{left:764px;background:#8a8f91}
.clients-nav.next{left:801px;background:var(--red)}
.client{top:896px;width:106px;height:56px;background:var(--white);display:flex;align-items:center;justify-content:center;font-size:11px;font-weight:700;color:#444;text-align:center;line-height:1.15;padding:0 6px}

.site-footer{left:0;top:984px;width:930px;height:186px;background:var(--teal)}
.footer-text{color:var(--white)}
.footer-brand{left:102px;top:1008px;font-size:18px;font-weight:700}
.footer-info{left:104px;top:1036px;width:300px;font-size:8.5px;line-height:1.45}
.footer-info b{font-size:10px;font-style:italic}
.footer-col{top:1010px}
.footer-col h3{font-size:13px;font-weight:600;margin-bottom:8px}
.footer-col li{list-style:none;font-size:8.5px;line-height:14.5px}
.footer-col li::before{content:"›";margin-right:6px}
.col-company{left:424px}.col-community{left:516px}
.blog-head{left:623px;top:1010px;font-size:13px}
.blog-head em{font-style:italic;font-weight:400}
.blog-post{left:622px;display:flex;gap:12px}
.blog-post .thumb{width:42px;height:42px;flex:none;background:linear-gradient(#6b4a3a,#2d2d2d)}
.blog-post p{font-size:8.5px;line-height:1.4;width:160px}
.blog-post small{display:block;font-size:8px;opacity:.85}
.bottom-bar{left:0;top:1170px;width:930px;height:30px;background:var(--teal-dark);color:var(--white)}
.copyright{left:102px;top:9px;font-size:8px}
.social{right:100px;top:8px;display:flex;gap:12px;font-size:9px;font-weight:600}
</style>
</head>
<body>
<header class="site-header abs">
  <div class="brand abs">KM Valero</div>
  <nav class="main-nav abs">
    <a class="active">Home</a><a>Products</a><a>About</a><a>Blog</a><a>Forum</a><a>Media Room</a><a>Success Stories</a><a>Contact Us</a><span style="width:22px"></span>
  </nav>
  <svg class="search-icon abs" width="11" height="11" viewBox="0 0 11 11"><circle cx="4.5" cy="4.5" r="3.3" fill="none" stroke="#fff" stroke-width="1.6"/><line x1="7" y1="7" x2="10" y2="10" stroke="#fff" stroke-width="1.8"/></svg>
</header>

<section class="hero abs" role="img" aria-label="Sunny sky and green meadow scene with two smiling women, one holding a bathroom scale"></section>
<div class="hero-person-left abs" role="img" aria-label="Woman in a dark dress"></div>
<div class="hero-person-right abs" role="img" aria-label="Woman in white sportswear holding a scale"></div>
<div class="hero-title abs">KM VALERO</div>
<div class="hero-text abs">KM Valero is a nutritionist and certified weight-loss expert, passionate relationship/life coach.</div>
<div class="hero-arrow prev abs"><svg width="14" height="12" viewBox="0 0 14 12"><path d="M7 1 2 6l5 5M12 1 7 6l5 5" fill="none" stroke="#fff" stroke-width="1.8"/></svg></div>
<div class="hero-arrow next abs"><svg width="14" height="12" viewBox="0 0 14 12"><path d="M2 1l5 5-5 5M7 1l5 5-5 5" fill="none" stroke="#fff" stroke-width="1.8"/></svg></div>
<div class="slider-dots abs"><span></span><span></span></div>

<div class="report abs"></div>
<div class="report-book abs" role="img" aria-label="Cover of the free report booklet"></div>
<div class="report-label abs">FREE Report:<br>"7 Habits Keeping the Scale Stuck!"</div>
<div class="report-note abs">Just enter your name and email below to get instant access to this 30 page report absolutely FREE!</div>
<div class="report-form abs">Name :<span class="field"></span>Email :<span class="field"></span><span class="subscribe">SUBSCRIBE</span></div>
<div class="privacy abs">E-mail Privacy: Sign up with complete confidence! We will never sell, rent, lease, or share your information with anyone.</div>

<div class="why-band abs"></div>
<h2 class="why-title abs">WHY KM VALERO ?</h2>
<p class="why-sub abs">KM Valero is a nutritionist and certified weight-loss expert, passionate relationship/life coach.</p>

<div class="card card-left abs"><span class="dots"><i></i><i></i><i></i></span><div class="photo" role="img" aria-label="Red apples and a bottle of vinegar" style="background:linear-gradient(135deg,#a83228,#6a8a3a,#c77a2a)"></div></div>
<div class="card card-right abs"><span class="bar"></span><div class="photo" role="img" aria-label="Hand holding an apple in front of a waist" style="background:linear-gradient(135deg,#e8d8cc,#d59a8a,#e9b7c2)"></div></div>
<div class="card card-main abs"><span class="dots"><i></i><i></i><i></i></span><span class="bar"></span><div class="photo" role="img" aria-label="Green apple wrapped in a measuring tape with a slimming tagline" style="background:radial-gradient(circle at 55% 45%,#9cc93a,#3f8a14 70%)"></div></div>

<div class="clients-title abs">Our Happy Clients</div>
<div class="clients-rule abs"></div>
<div class="clients-nav prev abs"><svg width="8" height="10"><path d="M6 1 2 5l4 4" fill="none" stroke="#fff" stroke-width="2"/></svg></div>
<div class="clients-nav next abs"><svg width="8" height="10"><path d="M2 1l4 4-4 4" fill="none" stroke="#fff" stroke-width="2"/></svg></div>
<div class="client abs" style="left:101px">Homestead Weekly</div>
<div class="client abs" style="left:224px">Corvane TV</div>
<div class="client abs" style="left:349px">Tessaly One</div>
<div class="client abs" style="left:473px">OrbitWave Radio</div>
<div class="client abs" style="left:598px">Halvern News</div>
<div class="client abs" style="left:721px">Pulse 212</div>

<footer class="site-footer abs"></footer>
<div class="footer-brand footer-text abs">KM VALERO</div>
<div class="footer-info footer-text abs">To book KM for TV, Radio or Speaking Engagements:<br>Media Email: info@kmvalerohub.com<br><b>Media Phone: 555-014-2290</b> (only media inquiries will get a return call)<br>Personal medical and health-related questions and inquiries will NOT receive a response.<br>For customer service support, contact <b>info@kmvalerohub.com</b><br>If you have questions on the Core Reset Plan or the book, please ask them on the FORUM on this website.</div>
<div class="footer-col col-company footer-text abs"><h3>Company</h3><ul><li>Home</li><li>Products</li><li>About</li><li>Blog</li><li>Forum</li><li>Media Room</li><li>Success Stories</li><li>Contact Us</li></ul></div>
<div class="footer-col col-community footer-text abs"><h3>Community</h3><ul><li>Log in</li><li>Entries Feed</li><li>Comments Feed</li><li>PressBase.org</li></ul></div>
<div class="blog-head footer-text abs"><em>from the</em> <b>BLOG</b></div>
<div class="blog-post footer-text abs" style="top:1040px"><div class="thumb" role="img" aria-label="Blog post photo"></div><p>Why I Chose to Thrive!<br>In case you were wondering, where in the<small>May 27, 2013</small></p></div>
<div class="blog-post footer-text abs" style="top:1096px"><div class="thumb" role="img" aria-label="Blog post photo"></div><p>1 Habit That's Quietly Stalling Your Weight-Loss Progress!<small>January 31, 2013</small></p></div>
<div class="bottom-bar abs">
  <div class="copyright abs">Copyright © 2014 KM Valero</div>
  <div class="social abs"><span>Linkly</span><span>Circlet</span><span>Chirpa</span><span>Feed</span></div>
</div>
</body>
</html>
```